Business card for law firm

Need business card for new law firm. Think confident, authoritative, conservative, but not stuffy or old-fashioned.

Contact Information for Business Card

Content for card - logo (uploaded), plus the following:

Paul Whitcombe (larger font)
Managing Partner (larger font, but not as large as name)
Level 9, 7 Ferris Lane
Sydney NSW 2000
Main Tel 02 9364 2710
Direct Tel 02 8472 3159
Email paul@qvlegal.com.au
www.qvlegal.com.au

Letterhead design should include logo plus:
Level 9, 7 Ferris Lane
Sydney NSW 2000
Tel 02 8472 3159
www.qvlegal.com.au

```html
<!DOCTYPE html>
<html lang="en">
<head>
<meta charset="utf-8">
<title>Quayvale Legal – Business Card</title>
<link href="https://fonts.googleapis.com/css2?family=Montserrat:wght@400;500;700&display=swap" rel="stylesheet">
<style>
  :root {
    --navy: #1f2a5c;
    --ink: #262a3d;
    --card: #ffffff;
    --backdrop-top: #e6e6e6;
    --backdrop-bottom: #bdbdbd;
    --rule: #2b3566;
  }
  * { box-sizing: border-box; margin: 0; padding: 0; }
  html, body {
    width: 1200px;
    height: 900px;
    overflow: hidden;
  }
  body {
    background: linear-gradient(180deg, var(--backdrop-top), var(--backdrop-bottom));
    display: flex;
    align-items: center;
    justify-content: center;
    font-family: "Montserrat", sans-serif;
  }
  .business-card {
    position: relative;
    width: 1000px;
    height: 572px;
    background: var(--card);
    box-shadow: 0 18px 40px rgba(0,0,0,0.25);
    display: flex;
    align-items: center;
  }
  .brand {
    width: 470px;
    display: flex;
    flex-direction: column;
    align-items: center;
    justify-content: center;
    gap: 26px;
  }
  .brand-square {
    width: 64px;
    height: 64px;
    background: var(--navy);
  }
  .brand-name {
    font-weight: 500;
    font-size: 40px;
    letter-spacing: 0.08em;
    text-transform: uppercase;
    color: var(--navy);
  }
  .divider {
    width: 2px;
    height: 300px;
    background: var(--rule);
  }
  .contact {
    padding-left: 52px;
    color: var(--navy);
  }
  .contact-name {
    font-weight: 700;
    font-size: 38px;
    line-height: 1.1;
  }
  .contact-role {
    font-weight: 400;
    font-size: 26px;
    margin-bottom: 18px;
  }
  .contact-address {
    font-size: 25px;
    line-height: 1.3;
    margin-bottom: 6px;
  }
  .contact-list {
    list-style: none;
    font-size: 25px;
    line-height: 1.35;
  }
  .contact-list li {
    display: flex;
    align-items: center;
    gap: 14px;
  }
  .contact-list svg {
    width: 20px;
    height: 20px;
    flex: none;
    fill: none;
    stroke: var(--navy);
    stroke-width: 2;
  }
</style>
</head>
<body>
  <div class="business-card">
    <div class="brand">
      <div class="brand-square"></div>
      <div class="brand-name">Quayvale Legal</div>
    </div>
    <div class="divider"></div>
    <div class="contact">
      <p class="contact-name">Paul Whitcombe</p>
      <p class="contact-role">Managing Partner</p>
      <p class="contact-address">Level 9, 7 Ferris Lane<br>Sydney NSW 2000</p>
      <ul class="contact-list">
        <li>
          <svg viewBox="0 0 24 24" aria-hidden="true"><path d="M6 3h4l2 5-3 2a11 11 0 0 0 5 5l2-3 5 2v4a2 2 0 0 1-2 2A17 17 0 0 1 4 5a2 2 0 0 1 2-2z"/></svg>
          02 9364 2710
        </li>
        <li>
          <svg viewBox="0 0 24 24" aria-hidden="true"><path d="M6 3h4l2 5-3 2a11 11 0 0 0 5 5l2-3 5 2v4a2 2 0 0 1-2 2A17 17 0 0 1 4 5a2 2 0 0 1 2-2z"/></svg>
          02 8472 3159
        </li>
        <li>
          <svg viewBox="0 0 24 24" aria-hidden="true"><rect x="3" y="6" width="18" height="12"/><path d="M3 6l9 7 9-7"/></svg>
          paul@qvlegal.com.au
        </li>
        <li>
          <svg viewBox="0 0 24 24" aria-hidden="true"><circle cx="12" cy="12" r="9"/><path d="M3 12h18M12 3c3 3 3 15 0 18M12 3c-3 3-3 15 0 18"/></svg>
          www.qvlegal.com.au
        </li>
      </ul>
    </div>
  </div>
</body>
</html>
```